Optimization existing Business Card

I need a revision of the business card, incl. Logo Design. I am a freelancer and have my headquarters in Berlin. I develop business consulting solutions for banks, insurance and StartUp Companies. I want a simple design of the business card. The final design should professionalism and commitment and openness to communicate. I'm open minded in addition to optimizing the existing logo / business card as well on a new idea / proposal for the logo. Idea would be for example the logo of this page: http://dravolt-partners.example.

Target Market(s)

Consulting, Banking, Investment Banking

Industry/Entity Type

Business

Contact Information for Business Card

siehe Anhang (please take a look into the attachments, important)

Font styles to use
Sans Serif

Requirements
Must have
• Please look at my specifications exactly !! (Please see my specifications), CEO Founder not
Should not have
• No gradient !! (No overarching color gradient)

```html
<!DOCTYPE html>
<html lang="de">
<head>
<meta charset="utf-8">
<title>Halvermoor Consulting – Visitenkarte</title>
<link href="https://fonts.googleapis.com/css2?family=Open+Sans:wght@400;600;700&display=swap" rel="stylesheet">
<style>
  :root {
    --stage: #2c2c2c;
    --brand-blue: #27a8e0;
    --brand-navy: #3b3b5c;
    --paper: #ffffff;
    --ink: #1d1d24;
  }
  html, body {
    margin: 0;
    width: 1200px;
    height: 1166px;
    overflow: hidden;
    background: var(--stage);
    font-family: "Open Sans", Arial, sans-serif;
  }
  .card {
    position: absolute;
    left: 160px;
    width: 880px;
    height: 503px;
    overflow: hidden;
    box-shadow: 0 12px 30px rgba(0,0,0,.45);
  }
  .card--front { top: 50px; background: var(--brand-blue); color: var(--paper); }
  .card--back { top: 613px; background: var(--paper); color: var(--ink); }

  .lockup { position: absolute; display: flex; align-items: center; gap: 18px; }
  .lockup__mark { width: 46px; height: 46px; border-radius: 50%; flex: none; }
  .lockup__name { font-weight: 700; font-size: 34px; line-height: 1.02; letter-spacing: .3px; }
  .lockup__divider { width: 2px; height: 64px; align-self: center; }
  .lockup__services { font-size: 12.5px; line-height: 1.3; text-transform: uppercase; letter-spacing: .4px; }

  .card--front .lockup { left: 190px; top: 200px; }
  .card--front .lockup__mark { background: var(--paper); }
  .card--front .lockup__divider { background: var(--paper); }

  .card--back .lockup { left: 50px; top: 90px; }
  .card--back .lockup__mark { background: var(--brand-blue); }
  .card--back .lockup__name { color: var(--brand-navy); }
  .card--back .lockup__divider { background: var(--brand-blue); }
  .card--back .lockup__services { color: var(--brand-navy); }

  .holder { position: absolute; right: 60px; top: 90px; text-align: right; }
  .holder__name { font-weight: 700; font-size: 26px; color: var(--brand-blue); margin: 0; }
  .holder__role { font-size: 15px; margin: 2px 0 0; }

  .address { position: absolute; left: 120px; top: 250px; font-size: 19px; line-height: 1.35; margin: 0; font-style: normal; }
  .contacts { position: absolute; left: 120px; top: 322px; list-style: none; margin: 0; padding: 0; font-size: 18px; line-height: 1.55; }
  .contacts li { display: flex; align-items: center; gap: 12px; }
  .contacts svg { width: 18px; height: 18px; flex: none; fill: var(--brand-blue); }

  .swoosh { position: absolute; inset: 0; }
  .website { font-size: 17px; fill: var(--paper); }
</style>
</head>
<body>

<section class="card card--front">
  <div class="lockup">
    <span class="lockup__mark"></span>
    <div class="lockup__name">halvermoor<br>consulting</div>
    <span class="lockup__divider"></span>
    <div class="lockup__services">Unternehmensberatung<br>Banking<br>Business Coaching</div>
  </div>
</section>

<section class="card card--back">
  <svg class="swoosh" viewBox="0 0 880 503" aria-hidden="false">
    <path d="M330 432 Q660 370 880 168 L880 186 Q660 392 330 436 Z" fill="var(--brand-navy)"/>
    <path d="M0 466 Q520 446 880 204 L880 503 L0 503 Z" fill="var(--brand-blue)"/>
    <text class="website" x="840" y="470" text-anchor="end">www.halvermoor-consulting.example</text>
  </svg>

  <div class="lockup">
    <span class="lockup__mark"></span>
    <div class="lockup__name">halvermoor<br>consulting</div>
    <span class="lockup__divider"></span>
    <div class="lockup__services">Unternehmensberatung<br>Banking<br>Business Coaching</div>
  </div>

  <div class="holder">
    <p class="holder__name">Lena Halvermoor</p>
    <p class="holder__role">CEO</p>
  </div>

  <address class="address">Lindenweg 48<br>10115 Berlin, Germany</address>

  <ul class="contacts">
    <li>
      <svg viewBox="0 0 24 24"><path d="M6.6 10.8a15.1 15.1 0 0 0 6.6 6.6l2.2-2.2a1 1 0 0 1 1-.25 11.4 11.4 0 0 0 3.6.57 1 1 0 0 1 1 1V20a1 1 0 0 1-1 1A17 17 0 0 1 3 4a1 1 0 0 1 1-1h3.5a1 1 0 0 1 1 1c0 1.25.2 2.45.57 3.57a1 1 0 0 1-.25 1z"/></svg>
      +49 (0) 30 5550 1842
    </li>
    <li>
      <svg viewBox="0 0 24 24"><path d="M7 2h10a2 2 0 0 1 2 2v16a2 2 0 0 1-2 2H7a2 2 0 0 1-2-2V4a2 2 0 0 1 2-2zm0 3v12h10V5zm5 14a1 1 0 1 0 0 2 1 1 0 0 0 0-2z"/></svg>
      +49 (0) 170 5550 9317
    </li>
    <li>
      <svg viewBox="0 0 24 24"><path d="M2 5h20v14H2zm2 2v.4l8 5.2 8-5.2V7zm0 2.8V17h16V9.8l-8 5.2z"/></svg>
      lh@halvermoor-consulting.example
    </li>
  </ul>
</section>

</body>
</html>
```